Professional Single Page Website Design for Tollbrook Advisory

Tollbrook Advisory is a new business consultancy specializing in providing expert services to small businesses, primarily in the brick-and-mortar retail and food service sectors. We offer a range of services including franchise development and launch, due diligence, and construction management.

Currently, we have a basic website set up at www.tollbrookadvisory.example, but we need a professional touch to enhance its design and functionality.

Project Requirements:
- Single Page Design: For now, we need a single page design that effectively showcases who we are, our services, and contact information.
- Future Expansion: The design should be flexible and scalable for future expansion to include additional pages like specific service offerings, about us, and a dedicated contact page.
- Design Aesthetic: We are looking for a modern yet professional design that aligns with our brand identity.
- Logo: We have a logo that we like, which was also sourced from Pixel Bazaar. The logo files are attached to this project brief.

Key Sections to Include:
- Hero Section: An engaging introduction to Tollbrook Advisory with a strong visual impact.
- About Us: A brief overview of who we are and our mission.
- Team: Section for the profiles of the two principals.
- Services: A clear and concise presentation of our services, including franchise development, due diligence, and construction management.
- Contact Information: Easy-to-find contact details, including a form for inquiries.
- Call to Action: Encouraging visitors to get in touch with us for consultations or further information.

Design Considerations:
- Ensure the design is responsive and mobile-friendly.
- Include high-quality images and icons that complement our services and industry.
- We do not need development services, this is only a design project.

```html
<!DOCTYPE html>
<html lang="en">
<head>
<meta charset="UTF-8">
<title>Tollbrook Advisory</title>
<link href="https://fonts.googleapis.com/css2?family=Poppins:wght@500;600;700&family=Montserrat:wght@400;500;600;700&display=swap" rel="stylesheet">
<style>
:root{
  --green:#7fbc9f;
  --green-text:#6aa98a;
  --band:#6fa88c;
  --dark:#1f2b34;
  --ink:#1d1d1d;
  --body:#4a4a4a;
  --muted:#6e6e6e;
  --white:#ffffff;
}
*{margin:0;padding:0;box-sizing:border-box}
html,body{width:1200px;height:3882px;overflow:hidden}
body{position:relative;background:var(--white);font-family:'Montserrat',sans-serif;color:var(--body)}
.abs{position:absolute}
.head{font-family:'Poppins',sans-serif;font-weight:700}
.btn{position:absolute;display:flex;align-items:center;justify-content:center;border-radius:24px;background:var(--green);color:var(--dark);font-family:'Poppins',sans-serif;font-weight:600;font-size:16px}

/* hero */
.hero{left:0;top:0;width:1200px;height:642px;background:linear-gradient(135deg,#3d4a4b 0%,#5a655f 35%,#2c3a3e 70%,#4a5250 100%)}
.hero-shade{left:0;top:0;width:1200px;height:642px;background:rgba(20,28,30,.35)}
.nav{left:15px;top:18px;width:1167px;height:85px;background:var(--white);border-radius:43px}
.brand{font-family:'Poppins',sans-serif;font-weight:600;color:var(--dark);font-size:22px;display:flex;align-items:center;gap:10px}
.brand-dot{width:40px;height:40px;border-radius:50%;background:var(--green)}
.nav-links{left:375px;top:52px;display:flex;gap:42px;font-size:13px;font-weight:500;color:var(--ink)}
.hero-title{left:0;width:1200px;text-align:center;font-size:54px;color:var(--white);line-height:66px}
.hero-title span{color:var(--green)}
.hero-sub{left:0;width:1200px;text-align:center;top:345px;font-size:31px;color:var(--white);line-height:43px;font-weight:500}

/* about */
.about-photo{left:104px;top:772px;width:461px;height:535px;border-radius:6px;background:linear-gradient(160deg,#9fb4c3 0%,#6d7f8b 45%,#8c7d6d 100%)}
.about-h{left:627px;font-size:39px;color:var(--ink)}
.about-p{left:627px;width:430px;font-size:14.5px;line-height:29px;color:var(--body)}
.about-p a{color:var(--green-text);font-weight:600;text-decoration:none}
.mission-h{left:627px;top:1120px;font-family:'Montserrat',sans-serif;font-size:22px;font-weight:500;color:var(--ink)}

/* services */
.services{left:0;top:1419px;width:1200px;height:642px;background:var(--band)}
.section-title{left:0;width:1200px;text-align:center;font-size:42px}
.card{top:1587px;width:307px;height:362px;background:var(--white);border-radius:6px;text-align:center}
.card-icon{position:absolute;left:100px;top:27px;width:107px;height:107px;border-radius:50%;background:var(--green)}
.card h3{position:absolute;left:0;width:100%;top:150px;font-size:19px;font-weight:600;color:var(--ink);line-height:33px}
.card p{position:absolute;left:30px;width:247px;top:228px;font-size:14.5px;line-height:29px;color:var(--muted)}
.card.feature{background:linear-gradient(160deg,#3e4a52 0%,#2b363d 60%,#37434a 100%)}
.card.feature .frame{position:absolute;left:9px;top:9px;right:9px;bottom:9px;border:2px dashed #e4e4e4}
.card.feature h3{top:50px;color:var(--white)}
.card.feature p{left:22px;width:263px;top:117px;color:#e8e8e8}
.card.feature p a{color:var(--green);font-weight:700}
.arrow{top:1747px;width:42px;height:42px;border:2.5px solid var(--white);border-radius:50%;background:transparent}
.arrow.right{border-color:var(--dark)}

/* team */
.team-card{left:131px;top:2248px;width:932px;height:407px;border:1.5px solid #9a9a9a;border-radius:6px;box-shadow:0 3px 8px rgba(0,0,0,.12)}
.team-photo{left:651px;top:2254px;width:404px;height:395px;border-radius:4px;background:linear-gradient(180deg,#9ec3e0 0%,#c9d2cf 45%,#e7e9ec 100%)}
.team-name{left:162px;top:2278px;font-family:'Montserrat',sans-serif;font-weight:600;font-size:32px;color:var(--dark)}
.team-role{left:163px;top:2330px;font-weight:600;font-size:21px;color:var(--dark)}
.team-bio{left:163px;top:2372px;width:478px;font-size:14.2px;line-height:29px;color:var(--muted)}
.team-btn{top:2590px;width:44px;height:44px;border:1.5px solid #9fcbb6;border-radius:6px;display:flex;align-items:center;justify-content:center;background:var(--white)}
.pager-bar{left:540px;top:2712px;width:51px;height:6px;border-radius:3px;background:var(--dark)}
.pager-dot{left:610px;top:2711px;width:9px;height:9px;border-radius:50%;background:var(--green-text)}

/* contact */
.contact{left:0;top:2828px;width:1200px;height:642px;background:var(--band)}
.label{font-size:15px;font-weight:600;color:var(--white)}
.field{background:var(--white);border:1px solid #d7d7d7;border-radius:4px}
.placeholder{font-size:12px;color:#333}
.submit{left:513px;top:3325px;width:170px;height:47px;background:var(--dark);color:var(--white)}

/* footer */
.footer{left:0;top:3470px;width:1200px;height:412px;background:var(--dark)}
.f-brand{left:108px;top:3585px;color:var(--green);font-size:22px}
.social{top:3697px;width:32px;height:32px;border-radius:50%;background:var(--white)}
.f-head{font-family:'Poppins',sans-serif;font-weight:500;font-size:21px;color:var(--white)}
.f-list{font-size:14px;color:var(--white);line-height:28.6px}
.f-contact{left:636px;top:3610px;font-size:14px;color:var(--white);line-height:28.6px}
.f-contact div{display:flex;align-items:center;gap:8px}
.f-contact svg{flex:none}
.map{left:888px;top:3601px;width:197px;height:189px;border-radius:4px;background:linear-gradient(135deg,#e9eef2 0%,#dfe6ea 50%,#f0ebdc 100%)}
.f-rule{left:107px;top:3827px;width:977px;height:1px;background:#cfd6da}
.copyright{left:0;width:1210px;text-align:center;top:3845px;font-size:13px;color:var(--white)}
</style>
</head>
<body>

<!-- Hero -->
<div class="abs hero" role="img" aria-label="Business team meeting around a table with laptops in a bright office overlooking the city"></div>
<div class="abs hero-shade"></div>

<header class="abs nav">
  <div class="abs brand" style="left:20px;top:22px"><span class="brand-dot"></span>Tollbrook Advisory</div>
  <nav class="abs nav-links" style="left:360px;top:35px">
    <span>HOME</span><span>ABOUT</span><span>SERVICES</span><span>OUR TEAM</span><span>CONTACT</span>
  </nav>
  <div class="btn" style="left:966px;top:19px;width:172px;height:47px">Get In Touch</div>
</header>

<h1 class="abs head hero-title" style="top:198px">Building <span>Success</span> in<br><span>Southern California</span></h1>
<p class="abs hero-sub">Expertise at Every Step: From<br>Planning to Execution</p>
<div class="btn" style="left:513px;top:455px;width:170px;height:47px">Learn More</div>

<!-- About -->
<div class="abs about-photo" role="img" aria-label="Two colleagues discussing documents at a desk in a modern office"></div>
<h2 class="abs head about-h" style="top:762px">About</h2>
<h2 class="abs head about-h" style="top:808px;color:var(--green-text)">Tollbrook Advisory</h2>
<p class="abs about-p" style="top:880px">Welcome to Tollbrook Advisory, your trusted partner in navigating the complexities of the real estate and small business markets. Founded by industry veterans Elias Moreno and Owen Hale, we specialize in providing comprehensive services tailored to the unique needs of our clients. Whether you're a franchisee, a new restaurant owner, or a commercial real estate investor, our expertise in due diligence, <a>Learn More..</a></p>
<h3 class="abs mission-h">Mission</h3>
<p class="abs about-p" style="top:1155px">Welcome to Tollbrook Advisory, your trusted partner in navigating the complexities of the real estate and small business markets. &nbsp;<a>Learn More..</a></p>
<div class="btn" style="left:621px;top:1271px;width:171px;height:46px">Learn More</div>

<!-- Services -->
<section class="abs services"></section>
<h2 class="abs head section-title" style="top:1490px;color:var(--white)">Tollbrook Services</h2>

<div class="abs card" style="left:108px">
  <div class="card-icon">
    <svg width="107" height="107" viewBox="0 0 107 107" fill="#1f2b34">
      <rect x="25" y="28" width="16" height="14" rx="2"/><rect x="66" y="28" width="16" height="14" rx="2"/>
      <rect x="45" y="46" width="16" height="14" rx="2"/>
      <rect x="25" y="65" width="16" height="14" rx="2"/><rect x="66" y="65" width="16" height="14" rx="2"/>
    </svg>
  </div>
  <h3>Franchise<br>Development &amp; Launch</h3>
  <p>Comprehensive franchise setup from evaluation to launch for scalable business growth.</p>
</div>

<div class="abs card feature" style="left:443px" role="img" aria-label="Construction site backdrop with service description">
  <div class="frame"></div>
  <h3>Building &amp; Construction<br>Management</h3>
  <p>Our Building &amp; Construction Management Services oversee every aspect of your construction and development projects, from initial planning to final completion. We ensure projects stay on time<br><a>Learn More..</a></p>
</div>

<div class="abs card" style="left:776px">
  <div class="card-icon">
    <svg width="107" height="107" viewBox="0 0 107 107" fill="#1f2b34">
      <circle cx="38" cy="38" r="11"/>
      <rect x="56" y="28" width="24" height="4"/><rect x="56" y="36" width="24" height="4"/><rect x="56" y="44" width="24" height="4"/>
      <rect x="26" y="60" width="6" height="20"/><rect x="36" y="54" width="6" height="26"/><rect x="46" y="64" width="6" height="16"/>
      <circle cx="64" cy="64" r="9" fill="none" stroke="#1f2b34" stroke-width="4"/>
      <rect x="70" y="72" width="5" height="12" transform="rotate(-45 72 78)"/>
    </svg>
  </div>
  <h3>Market Analysis &amp;<br>Feasibility Studies</h3>
  <p>Conducting comprehensive market research to assess the viability of real estate.</p>
</div>

<div class="abs arrow" style="left:23px">
  <svg width="37" height="37" viewBox="0 0 37 37"><path d="M21 11 L14 18.5 L21 26" fill="none" stroke="#fff" stroke-width="2.5"/></svg>
</div>
<div class="abs arrow right" style="left:1137px">
  <svg width="37" height="37" viewBox="0 0 37 37"><path d="M16 11 L23 18.5 L16 26" fill="none" stroke="#1f2b34" stroke-width="2.5"/></svg>
</div>

<!-- Team -->
<h2 class="abs head section-title" style="top:2140px;color:var(--ink)">Our <span style="color:var(--green-text)">Leadership Team</span></h2>
<div class="abs team-card"></div>
<div class="abs team-photo" role="img" aria-label="Portrait of the principal on a rooftop terrace with hills behind"></div>
<h3 class="abs team-name">Elias Moreno</h3>
<p class="abs head team-role" style="font-family:'Montserrat',sans-serif">Principal</p>
<p class="abs team-bio">Elias Moreno brings almost 20 years of rich experience as a real estate investor and a pivotal role at one of southern California's largest real estate management firms, where he led sales and marketing strategies to elevate property value and investor returns. His vast expertise spans through strategic development and market analysis, making him a cornerstone for Tollbrook Advisory.....</p>
<div class="abs team-btn" style="left:166px">
  <svg width="22" height="22" viewBox="0 0 24 24"><path d="M6.6 10.8c1.4 2.8 3.8 5.1 6.6 6.6l2.2-2.2c.3-.3.7-.4 1-.2 1.1.4 2.3.6 3.6.6.6 0 1 .4 1 1V20c0 .6-.4 1-1 1C10.6 21 3 13.4 3 4c0-.6.4-1 1-1h3.5c.6 0 1 .4 1 1 0 1.3.2 2.5.6 3.6.1.3 0 .7-.2 1L6.6 10.8z" fill="#6aa98a"/></svg>
</div>
<div class="abs team-btn" style="left:242px">
  <svg width="22" height="22" viewBox="0 0 24 24"><rect x="3" y="5" width="18" height="14" rx="1.5" fill="#6aa98a"/><path d="M3.5 6 L12 13 L20.5 6" fill="none" stroke="#fff" stroke-width="1.6"/></svg>
</div>
<div class="abs pager-bar"></div>
<div class="abs pager-dot"></div>

<!-- Contact -->
<section class="abs contact"></section>
<h2 class="abs head section-title" style="top:2910px;color:var(--white)">Get InTouch</h2>
<form>
  <span class="abs label" style="left:145px;top:2994px">Name</span>
  <span class="abs label" style="left:457px;top:2994px">Phone Number</span>
  <span class="abs label" style="left:769px;top:2994px">Email</span>
  <div class="abs field" style="left:139px;top:3022px;width:297px;height:46px"></div>
  <div class="abs field" style="left:451px;top:3022px;width:297px;height:46px"></div>
  <div class="abs field" style="left:763px;top:3022px;width:295px;height:46px"></div>
  <span class="abs label" style="left:145px;top:3083px">Company</span>
  <div class="abs field" style="left:139px;top:3111px;width:919px;height:46px"></div>
  <span class="abs label" style="left:145px;top:3171px">Comment</span>
  <div class="abs field" style="left:139px;top:3200px;width:919px;height:88px"></div>
  <span class="abs placeholder" style="left:152px;top:3210px">Type Here</span>
  <div class="btn submit">Submit</div>
</form>

<!-- Footer -->
<footer class="abs footer"></footer>
<div class="abs brand f-brand"><span class="brand-dot" style="width:34px;height:34px"></span>Tollbrook Advisory</div>
<div class="abs social" style="left:124px"></div>
<div class="abs social" style="left:167px"></div>
<div class="abs social" style="left:210px"></div>

<h4 class="abs f-head" style="left:407px;top:3554px">Page Links</h4>
<div class="abs f-list" style="left:410px;top:3608px">Home<br>About<br>Services<br>Team<br>Contact</div>

<h4 class="abs f-head" style="left:632px;top:3554px">Contact Details</h4>
<div class="abs f-contact">
  <div><svg width="12" height="12" viewBox="0 0 24 24"><path d="M6.6 10.8c1.4 2.8 3.8 5.1 6.6 6.6l2.2-2.2c.3-.3.7-.4 1-.2 1.1.4 2.3.6 3.6.6.6 0 1 .4 1 1V20c0 .6-.4 1-1 1C10.6 21 3 13.4 3 4c0-.6.4-1 1-1h3.5c.6 0 1 .4 1 1 0 1.3.2 2.5.6 3.6.1.3 0 .7-.2 1L6.6 10.8z" fill="#fff"/></svg>+1 555 010 2040</div>
  <div><svg width="13" height="11" viewBox="0 0 24 20"><rect x="1" y="2" width="22" height="16" fill="#fff"/><path d="M1.5 3 L12 11 L22.5 3" fill="none" stroke="#1f2b34" stroke-width="2"/></svg>info@tollbrookadvisory.example</div>
  <div><svg width="12" height="14" viewBox="0 0 24 28"><path d="M12 1C6.5 1 2 5.5 2 11c0 7.5 10 16 10 16s10-8.5 10-16C22 5.5 17.5 1 12 1z" fill="#fff"/><circle cx="12" cy="11" r="4" fill="#1f2b34"/></svg>214 Meridian Ave,</div>
  <div style="padding-left:20px">Irvine, CA 92600</div>
</div>

<h4 class="abs f-head" style="left:935px;top:3549px">Location</h4>
<div class="abs map" role="img" aria-label="Street map showing the office location"></div>

<div class="abs f-rule"></div>
<p class="abs copyright">© 2024 Tollbrook Advisory I All Rights Reserved</p>

</body>
</html>
```